business card deign

Logo needs the following on it.
1. attached logo
2. Tagline - "If it chills a drink or lifts the night...we bring it!"
3. Name- Dalton Pikes, Founder and CPO
4. Address - 412 E. Carver Avenue, Ste 2207, Tampa, FL. 33917
5. Phone - 555.318.4726

```html
<!DOCTYPE html>
<html lang="en">
<head>
<meta charset="utf-8">
<title>Hopwell Business Card</title>
<link rel="stylesheet" href="https://fonts.googleapis.com/css2?family=Montserrat:wght@400;500;700&display=swap">
<style>
  :root {
    --backdrop: #e8e6e8;
    --card: #222222;
    --strip: #ffffff;
    --text-light: #ffffff;
    --text-soft: #e4e4e4;
    --tagline: #cfcfcf;
    --brand-dark: #0f0f0f;
    --art-top: #7a7a7a;
    --art-bottom: #151515;
  }
  * { margin: 0; padding: 0; box-sizing: border-box; }
  html, body {
    width: 1200px;
    height: 1108px;
    overflow: hidden;
    background: var(--backdrop);
    font-family: "Montserrat", sans-serif;
  }
  .card {
    position: absolute;
    width: 740px;
    height: 444px;
    background: var(--card);
    overflow: hidden;
  }
  .card::after {
    content: "";
    position: absolute;
    left: 0; right: 0; bottom: 0;
    height: 16px;
    background: var(--strip);
  }
  .card--front { left: 241px; top: 68px; }
  .card--back  { left: 248px; top: 589px; height: 443px; }

  .brand-name {
    position: absolute;
    left: 37px;
    top: 66px;
    color: var(--text-light);
    font-weight: 700;
    font-size: 40px;
    letter-spacing: 11px;
    line-height: 1;
  }
  .person {
    position: absolute;
    right: 47px;
    top: 56px;
    text-align: right;
    color: var(--text-light);
  }
  .person__name { font-weight: 700; font-size: 26px; line-height: 1.2; }
  .person__role { font-weight: 400; font-size: 16px; color: var(--text-soft); margin-top: 1px; letter-spacing: 0.3px; }
  .side-tab {
    position: absolute;
    right: 0;
    top: 60px;
    width: 21px;
    height: 48px;
    background: var(--strip);
  }
  .address {
    position: absolute;
    left: 35px;
    top: 243px;
    color: var(--text-soft);
    font-size: 16px;
    line-height: 20px;
  }
  .contacts {
    position: absolute;
    left: 35px;
    top: 318px;
    list-style: none;
    color: var(--text-soft);
    font-size: 16px;
  }
  .contacts li {
    display: flex;
    align-items: center;
    height: 32px;
  }
  .contacts svg { width: 17px; height: 17px; margin-right: 9px; fill: var(--text-soft); }

  .mascot-art {
    position: absolute;
    background: linear-gradient(160deg, var(--art-top) 0%, #3a3a3a 40%, var(--art-bottom) 100%);
    opacity: 0.75;
  }
  .mascot-art--front {
    left: 330px; top: 152px; width: 365px; height: 276px;
    border-radius: 60% 40% 0 0 / 70% 50% 0 0;
  }
  .mascot-art--back {
    left: 212px; top: 60px; width: 260px; height: 196px;
    border-radius: 60% 40% 0 0 / 70% 50% 0 0;
  }
  .back-brand {
    position: absolute;
    left: 0; right: 0;
    top: 276px;
    text-align: center;
    color: var(--brand-dark);
    font-weight: 700;
    font-size: 42px;
    letter-spacing: 12px;
    padding-left: 12px;
    line-height: 1;
  }
  .tagline {
    position: absolute;
    left: 0; right: 0;
    top: 386px;
    text-align: center;
    color: var(--tagline);
    font-size: 16.5px;
  }
</style>
</head>
<body>
  <section class="card card--front">
    <div class="brand-name">HOPWELL</div>
    <div class="person">
      <div class="person__name">Dalton Pikes</div>
      <div class="person__role">Founder and CPO</div>
    </div>
    <div class="side-tab"></div>
    <div class="mascot-art mascot-art--front" role="img" aria-label="Large soft grey mascot illustration"></div>
    <p class="address">412 E. Carver Avenue, Ste 2207,<br>Tampa, FL. 33917</p>
    <ul class="contacts">
      <li>
        <svg viewBox="0 0 24 24" aria-hidden="true"><path d="M6.6 10.8a15.1 15.1 0 0 0 6.6 6.6l2.2-2.2c.3-.3.7-.4 1-.2 1.1.4 2.3.6 3.6.6.6 0 1 .4 1 1V20c0 .6-.4 1-1 1A17 17 0 0 1 3 4c0-.6.4-1 1-1h3.5c.6 0 1 .4 1 1 0 1.3.2 2.5.6 3.6.1.3 0 .7-.2 1z"/></svg>
        555.318.4726
      </li>
      <li>
        <svg viewBox="0 0 24 24" aria-hidden="true"><path d="M3 6.5V19h18V6.5l-9 6.8z"/><path d="M3 5h18l-9 6.8z"/></svg>
        info@hopwell.com
      </li>
      <li>
        <svg viewBox="0 0 24 24" aria-hidden="true"><circle cx="12" cy="12" r="9" fill="none" stroke="#e4e4e4" stroke-width="2"/><path d="M7 7c2 1 2 3 4 3s1 3 3 3-1 4-2 5c-2-1-3-3-3-5S5 11 5 9z"/><path d="M14 5c1 1 3 1 4 3s-2 2-3 1-2-2-1-4z"/></svg>
        www.hopwell.com
      </li>
    </ul>
  </section>

  <section class="card card--back">
    <div class="mascot-art mascot-art--back" role="img" aria-label="Soft grey mascot illustration above the brand name"></div>
    <div class="back-brand">HOPWELL</div>
    <p class="tagline">If it chills a drink or lifts the night...we bring it</p>
  </section>
</body>
</html>
```